Velmora Gems - High end custom Jewelry website

I need a web design for an online custom jewelry company called Velmora Gems. (www.velmoragems-demo.com) this company specializes in high-end custom made engagement rings, wedding bands and jewelry of all kinds (necklaces, earrings, bracelets etc)All our jewelry uses diamonds so there must be a focus on diamonds on every type of jewelry we will be designing off the website.

We are a company located in New York City but our website will
aim to cater to international, national clients and as well as New York city residents.The company low overhead provides diamonds and precious metal at a discounted costs compared to its competitors. Velmora Gems makes unique custom diamond jewelry of a higher quality and at a lower price than carriage trade retail jewellers. (meaning that our company allows our customers to save money on diamond jewelry then they would if they bought from any known store or company)

The website will act as a tool for our customers to create their own jewelry. The way they will do this is by uploading pictures of what they like, they can post any pictures they want (from drawings, to actual copy and pasted pictures from other websites of designs) From these designs we will create a 3D digital image of the jewelry they like and customize it - however they want (colours, size etc) and then give them a quote in price. From the quote they will either approve it and we can have it made for them in 1 weeks time. If they decline it we will try to do whatever it is they want for the design to suit their needs.

We want the website to be simple and user friendly since people will be working on it to create their own individual jewelry pieces. Therefore some useful headings should include:

"Custom Jewellery" or something like "your design" "Custom Design"

a drop heading here should show the following steps into creating the jewelry.

step 1:
upload pictures of the designs you like
step 2:
What is your ring size?
Step 3:
What setting would you like your ring in? platinum, 14k etc..
Step 4:
What is your budget?
Step 5 :
Once you’ve uploaded pictures and give an explanation of what you want then we will contact you by phone or email and proceed to design your ring. Give us your contact info in this step.

Other then that other headings id like to see on the site are:

"Home"
main page with appealing picture which I can later add text to it explaining our company

"About us"
will include a brief section of who we are

"Wedding/engagment"

We are based in New York City and our company offers a one-to-one personal service to our clients ensuring their expectations are well met and, if we can help it, surpassed. We are a personal shopping and diamond supplier to individuals. Custom design is our speciality weather it be wedding ring, engagement ring or anniversary ring we aim to create distinctive designs that both reflect your personality as well as the beauty of the gemstones used in your piece. We use platinum, 14l-18k gold and diamonds to whatever it is that you may desire.
We in our company believe that we are privileged to be a part of one of the biggest events in our customer’s lives, and we pride ourselves on making sure that our customers have the best experience possible. As the diamond is the center piece of every engagement ring, we at VG make sure that our clients find the best diamond possible that is within their budget. Similarly, we work with established jewellery artisans from Belgium to provide the highest possible craftsmanship to a ring design of your choice. We make sure that our rings are made by the true and tried traditional methods focused on quality rather than quantity and of course our diamonds are QRB certified.

Diamonds

A section that explains where our diamonds come from. A heading will drop down here that is a diamond guide, as shown below.
Diamond Guide

An overview of the 4 C’s and different settings, a section for a brief education on diamonds.
Client Experiences

A section where clients share their experiences with Velmora Gems and can post pictures and share stories about their engagement etc.

The colour i would like to see are white and black, white and dark blue or royal blue. I don't think pastel colours will look good with this, maybe accents of purple or something pastel but for the main colours I want to keep it classic and sophisticated since it is a diamond company.

"Sign in | Check out"
where users are able to create a profile and upload their pictures and create their designs..

and a "search section"

or something along these lines or if you can incorporate both:

Exquisite craftsmanship Finest quality diamonds
Will beat any competitors price by twenty to seventy percent guaranteed
Price quotes whitin24 hours

Upload design picture or sketch
Receive price quote within 24hours
Receive and approve free customized design
Receive you jewelry in 1 week or less

Engagment Ring or necklace, earring, etc
Name
EMail
phone
Competitior Link
Budget

The final design should communicate that Velmora Gems is a custom jewelry site that allows individuals to personalize any type of jewellery they want with diamonds - at a fraction of the cost in comparison to any other out there. Our team works very hard to ensure that you will be so involved in the custom order process that there is no chance of something not being made to your requests. Jewelry is made to the highest standard or it does not ship in the first place. In the event a custom order does not suit a customer, we will take returns within 14 days of delivery less a 25% restocking fee.

Target Market(s)

middle class and upper class people ages 25-45

Industry/Entity Type

Digital

Requirements
Must have
• We have the logo now that I will attach BUT if you want to design something else please feel free ! I am open to all designs and ideas.
My logo now is simply a sketch so even if we make it look a bit more professional and classy I would like that, I think I want to keep it simple just black and white and maybe make the diamond shiny if possible. other then black in white I liked the gold and black combination too.. but as I said open to any other creative ideas!

can take pictures of jewelry off this website:
http://www.plinthwaredesigns.example/library/rings.html
Nice to have
• We already have a logo but we would like to see a banner or something that indicated saving money on diamond jewelry without it looking tacky or too cheap..

Also would like to see artistic pictures if you can of jewelry alongside very simple designs of jewelry that the masses like, (anything trendy or appealing to the eye)

cursive or elegant writing could be nice, flash could also be incorporated in the main page..

Should not have
• Nothing to old fashioned, when I mean elegant maybe just the the name of the company in cursive writing (Velmora Gems) but the actual headings and font on the website to be in a widely used font on jewelry websites. Please no hot pink colours or anything neon..
no times new roman font..

```html
<!DOCTYPE html>
<html lang="en">
<head>
<meta charset="utf-8">
<title>Velmora Gems – Custom Diamond Jewellery</title>
<link rel="stylesheet" href="https://fonts.googleapis.com/css2?family=Open+Sans:wght@400;600;700&family=Cormorant+Garamond:wght@500&display=swap">
<style>
:root{
  --page:#f4eedd;
  --ink:#1a1a1a;
  --nav:#1b1b1b;
  --nav-text:#f1f1f1;
  --muted:#6e6a5f;
  --accent:#1e9be0;
  --accent-dark:#127bbd;
  --panel:#0d2c56;
  --panel-line:#26507f;
  --footer:#181818;
  --footer-text:#d8d8d8;
  --photo-dark:#0c0d12;
  --photo-mid:#3a4150;
}
*{box-sizing:border-box;margin:0;padding:0}
html,body{width:900px;height:1200px;overflow:hidden}
body{background:var(--page);font-family:"Open Sans",Arial,sans-serif;color:var(--ink);position:relative}
.site{position:relative;width:900px;height:1200px}

/* header */
.brand{position:absolute;top:40px;left:0;width:900px;text-align:center}
.brand-mark{display:inline-block;width:46px;height:46px;border-radius:50%;border:2px solid var(--ink)}
.brand-name{display:block;margin-top:8px;font-family:"Cormorant Garamond",Georgia,serif;font-weight:500;font-size:15px;letter-spacing:2px;color:var(--ink)}

.main-nav{position:absolute;top:135px;left:100px;width:704px;height:30px;background:var(--nav);display:flex;align-items:center;padding:0 12px}
.main-nav a{color:var(--nav-text);text-decoration:none;font-size:12px;font-weight:600;padding:0 10px;line-height:30px}
.main-nav a.current{background:#333}
.search{margin-left:auto;display:flex;align-items:center;width:130px;height:20px;background:#fff;border-radius:2px;padding:0 6px;font-size:11px;color:#555}
.search svg{margin-left:auto}

/* hero */
.hero{position:absolute;top:180px;left:100px;width:704px;height:345px;overflow:hidden;background:radial-gradient(ellipse at 50% 35%,var(--photo-mid) 0%,#181b23 50%,var(--photo-dark) 100%)}
.hero-photo{position:absolute;inset:0}
.hero-caption{position:absolute;left:0;bottom:0;width:100%;height:58px;background:rgba(10,10,12,.82);display:flex;align-items:center;padding:0 14px}
.hero-title{font-size:23px;font-weight:600;color:#fff;width:420px}
.hero-text{font-size:8px;line-height:11px;color:#bbb;width:160px}
.btn{display:inline-block;background:var(--accent);color:#fff;font-size:10px;font-weight:600;border-radius:3px;text-align:center;border-bottom:2px solid var(--accent-dark)}
.hero-caption .btn{margin-left:auto;padding:6px 14px}
.slide-arrow{position:absolute;top:310px;width:20px;height:32px;background:#1d1d1d;display:flex;align-items:center;justify-content:center}
.slide-arrow.left{left:100px}
.slide-arrow.right{left:784px}

/* products */
.section-title{position:absolute;left:0;width:900px;text-align:center;font-size:19px;font-weight:700}
.products-title{top:546px}
.products{position:absolute;top:588px;left:100px;width:704px;display:flex;justify-content:space-between}
.product{width:148px;text-align:center}
.product-photo{width:148px;height:118px;border:3px solid #fff;box-shadow:0 1px 3px rgba(0,0,0,.35);background:radial-gradient(ellipse at 50% 45%,#5b6170 0%,#1c1e24 55%,#08090c 100%)}
.product-name{margin-top:7px;font-size:14px;font-weight:700}
.product-text{margin-top:3px;font-size:8px;line-height:11px;color:var(--muted);padding:0 14px}
.product .btn{margin-top:9px;padding:4px 12px}
.row-arrow{position:absolute;top:630px}
.row-arrow.left{left:62px}
.row-arrow.right{left:820px}

/* welcome */
.welcome{position:absolute;top:860px;left:100px;width:520px}
.welcome-photo{position:absolute;top:0;left:0;width:166px;height:92px;background:linear-gradient(135deg,#2c2f38 0%,#0e0f13 60%,#4a4f5c 100%)}
.welcome-body{position:absolute;top:0;left:178px;width:342px}
.welcome-title{font-size:15px;font-weight:700;margin-bottom:6px}
.welcome p{font-size:8px;line-height:11px;color:var(--muted)}
.welcome-more{position:absolute;top:100px;left:0;width:520px}
.welcome .btn{position:absolute;top:160px;left:446px;padding:4px 12px}

/* enquiry panel */
.enquiry{position:absolute;top:860px;left:640px;width:164px;height:196px;background:var(--panel);padding:8px 9px}
.enquiry-title{color:#fff;font-size:12px;font-weight:700;margin-bottom:6px}
.field{height:17px;background:#fff;border:1px solid var(--panel-line);margin-bottom:5px;font-size:8px;color:#666;padding:0 5px;line-height:16px;display:flex;align-items:center}
.field svg{margin-left:auto}
.enquiry .btn{float:right;padding:4px 12px;margin-top:3px}

/* footer */
.site-footer{position:absolute;top:1080px;left:0;width:900px;height:120px;background:var(--footer)}
.footer-info{position:absolute;top:22px;left:100px;font-size:10px;line-height:15px;color:var(--footer-text)}
.social{position:absolute;top:82px;left:100px;display:flex;gap:6px}
.social span{width:14px;height:14px;border-radius:2px;background:#8d8d8d}
.promises{position:absolute;top:16px;left:548px;list-style:none;font-size:9px;line-height:12px;color:var(--footer-text)}
.promises li{position:relative;padding-left:14px;margin-bottom:8px;width:240px}
.promises li::before{content:"";position:absolute;left:0;top:3px;border-left:6px solid #fff;border-top:3px solid transparent;border-bottom:3px solid transparent}
</style>
</head>
<body>
<div class="site">

  <header class="brand">
    <span class="brand-mark"></span>
    <span class="brand-name">VELMORA GEMS</span>
  </header>

  <nav class="main-nav">
    <a class="current" href="#">Home</a>
    <a href="#">About us</a>
    <a href="#">Services</a>
    <a href="#">Gallery</a>
    <a href="#">Blog</a>
    <a href="#">Testimonials</a>
    <a href="#">Contact us</a>
    <div class="search">Search...
      <svg width="10" height="10" viewBox="0 0 10 10"><circle cx="4" cy="4" r="3" fill="none" stroke="#333" stroke-width="1.4"/><line x1="6.2" y1="6.2" x2="9.3" y2="9.3" stroke="#333" stroke-width="1.4"/></svg>
    </div>
  </nav>

  <section class="hero">
    <div class="hero-photo" role="img" aria-label="Row of five diamond engagement rings on a dark reflective surface"></div>
    <div class="hero-caption">
      <div class="hero-title">Create your own Jewellery</div>
      <div class="hero-text">Sed ut perspiciatis unde omnis iste natus error sit voluptatem accusantium dolore.</div>
      <a class="btn" href="#">Custom Jewellery</a>
    </div>
  </section>
  <div class="slide-arrow left"><svg width="8" height="12" viewBox="0 0 8 12"><path d="M7 1 2 6l5 5" fill="none" stroke="#fff" stroke-width="2"/></svg></div>
  <div class="slide-arrow right"><svg width="8" height="12" viewBox="0 0 8 12"><path d="M1 1l5 5-5 5" fill="none" stroke="#fff" stroke-width="2"/></svg></div>

  <h2 class="section-title products-title">Latest Products</h2>
  <svg class="row-arrow left" width="16" height="30" viewBox="0 0 16 30"><path d="M14 2 3 15l11 13" fill="none" stroke="#1a1a1a" stroke-width="4"/></svg>
  <svg class="row-arrow right" width="16" height="30" viewBox="0 0 16 30"><path d="M2 2l11 13L2 28" fill="none" stroke="#1a1a1a" stroke-width="4"/></svg>
  <section class="products">
    <article class="product">
      <div class="product-photo" role="img" aria-label="Diamond solitaire ring on black"></div>
      <h3 class="product-name">Product Name</h3>
      <p class="product-text">Sed ut perspiciatis unde omnis iste natus sit voluptatem</p>
      <a class="btn" href="#">Get Retail!</a>
    </article>
    <article class="product">
      <div class="product-photo" role="img" aria-label="Diamond halo ring on black"></div>
      <h3 class="product-name">Product Name</h3>
      <p class="product-text">Sed ut perspiciatis unde omnis iste natus sit voluptatem</p>
      <a class="btn" href="#">Get Retail!</a>
    </article>
    <article class="product">
      <div class="product-photo" role="img" aria-label="Pavé diamond ring on black"></div>
      <h3 class="product-name">Product Name</h3>
      <p class="product-text">Sed ut perspiciatis unde omnis iste natus sit voluptatem</p>
      <a class="btn" href="#">Get Retail!</a>
    </article>
    <article class="product">
      <div class="product-photo" role="img" aria-label="Three-stone diamond ring on black"></div>
      <h3 class="product-name">Product Name</h3>
      <p class="product-text">Sed ut perspiciatis unde omnis iste natus sit voluptatem</p>
      <a class="btn" href="#">Get Retail!</a>
    </article>
  </section>

  <section class="welcome">
    <div class="welcome-photo" role="img" aria-label="Scattered loose diamonds on a dark surface"></div>
    <div class="welcome-body">
      <h2 class="welcome-title">Welcome to Our Site...</h2>
      <p>Sed ut perspiciatis unde omnis iste natus error sit voluptatem accusantium doloremque laudantium, totam rem aperiam, eaque ipsa quae ab illo inventore veritatis et quasi architecto beatae vitae dicta sunt explicabo. Nemo enim ipsam voluptatem quia voluptas sit aspernatur aut odit aut fugit, sed quia consequuntur magni dolores eos qui ratione voluptatem sequi nesciunt.</p>
    </div>
    <p class="welcome-more">Sed ut perspiciatis unde omnis iste natus error sit voluptatem accusantium doloremque laudantium, totam rem aperiam, eaque ipsa quae ab illo inventore veritatis et quasi architecto beatae vitae dicta sunt explicabo nemo enim.</p>
    <a class="btn" href="#">Read More</a>
  </section>

  <aside class="enquiry">
    <h2 class="enquiry-title">Engagement Ring</h2>
    <div class="field">Name</div>
    <div class="field">Email</div>
    <div class="field">Phone</div>
    <div class="field">Competitor link</div>
    <div class="field">Budget
      <svg width="7" height="5" viewBox="0 0 7 5"><path d="M0 0h7L3.5 5z" fill="#555"/></svg>
    </div>
    <a class="btn" href="#">Submit</a>
  </aside>

  <footer class="site-footer">
    <div class="footer-info">2013 Velmora Gems. All Right Reserved<br>Privacy Policy</div>
    <div class="social"><span></span><span></span><span></span><span></span></div>
    <ul class="promises">
      <li>Exquisite craftsmanship Finest quality diamonds</li>
      <li>Will beat any competitors price by twenty to seventy percent guaranteed</li>
      <li>Price quotes within 24 hours</li>
    </ul>
  </footer>

</div>
</body>
</html>
```